OBK Farcoast Logistics Limited

We need the buissnes card to be very exclusive. As we are all young in our company. We need this to be the gate to make our clients feel deep interest for us.

We are focused in as International Trade advisors, and our products go from Oil Tanker Ships to Rubber balls for dogs.

Our Slogan is Bringing Trade Home.
And our main marketing will be through Internet.

We were stablished in 2009 In Mexico and we also have offices in Hong Kong.
We have representatives in China and Europe.

Target Market(s)

Is every company or Individual that wants to develop an International Project or product development or Logistic service of Goods and people.
Some of our current projects are Ship Brokerage, Mine Brokerage, Real State and Product Pormotional development.

Industry/Entity Type

It Company

Requirements
Must have
• Our Logo and slogan, and make the card accoriding to the logo.
Nice to have
• Our Colors

```html
<!DOCTYPE html>
<html lang="en">
<head>
<meta charset="utf-8">
<title>Business Card – Front and Back</title>
<link href="https://fonts.googleapis.com/css2?family=Source+Sans+3:wght@400;600;700&display=swap" rel="stylesheet">
<style>
  :root {
    --page: #ececec;
    --card-white: #ffffff;
    --brand-blue: #1b7fc0;
    --band-blue: #1f7dbb;
    --deep-blue: #176fae;
    --brand-green: #8cc63f;
    --ink: #222222;
    --white: #ffffff;
    --soft-circle: #d6e9f5;
  }
  * { margin: 0; padding: 0; box-sizing: border-box; }
  html, body {
    width: 1200px;
    height: 989px;
    overflow: hidden;
  }
  body {
    background: var(--page);
    font-family: "Source Sans 3", Arial, sans-serif;
    position: relative;
  }
  .card {
    position: absolute;
    width: 495px;
    height: 864px;
    overflow: hidden;
    box-shadow: 0 2px 8px rgba(0,0,0,0.18);
  }

  /* Front */
  .card-front {
    left: 73px;
    top: 52px;
    background: var(--card-white);
  }
  .brand-dot {
    position: absolute;
    left: 122px;
    top: 62px;
    width: 250px;
    height: 250px;
    border-radius: 50%;
    background: var(--soft-circle);
  }
  .front-name {
    position: absolute;
    left: 0;
    width: 100%;
    top: 340px;
    text-align: center;
    font-weight: 700;
    font-size: 116px;
    line-height: 1;
    color: var(--brand-green);
    letter-spacing: 6px;
  }
  .front-slogan {
    position: absolute;
    left: 0;
    width: 100%;
    top: 448px;
    text-align: center;
    font-size: 21px;
    color: var(--brand-blue);
  }
  .address {
    position: absolute;
    left: 0;
    width: 100%;
    top: 592px;
    text-align: center;
    font-size: 20px;
    color: var(--ink);
  }
  .divider {
    position: absolute;
    left: 0;
    width: 100%;
    top: 629px;
    height: 2px;
    background: var(--band-blue);
    opacity: 0.6;
  }
  .contact-band {
    position: absolute;
    left: 0;
    bottom: 0;
    width: 100%;
    height: 224px;
    background: var(--band-blue);
    color: var(--white);
    padding: 22px 0 0 38px;
  }
  .person {
    font-size: 20px;
    margin-bottom: 22px;
  }
  .person strong {
    font-size: 26px;
    font-weight: 700;
  }
  .contact-list { list-style: none; }
  .contact-list li {
    display: flex;
    align-items: center;
    font-size: 20px;
    height: 33px;
  }
  .contact-list svg {
    width: 18px;
    height: 18px;
    margin-right: 14px;
    fill: var(--white);
    flex: none;
  }

  /* Back */
  .card-back {
    left: 617px;
    top: 62px;
    background: var(--brand-blue);
    color: var(--white);
  }
  .back-dot {
    position: absolute;
    left: 40px;
    top: 250px;
    width: 415px;
    height: 415px;
    border-radius: 50%;
    background: var(--deep-blue);
    opacity: 0.55;
  }
  .back-name {
    position: absolute;
    left: 0;
    width: 100%;
    top: 302px;
    text-align: center;
    font-weight: 700;
    font-size: 186px;
    line-height: 1;
    letter-spacing: 10px;
  }
  .back-slogan {
    position: absolute;
    left: 0;
    width: 100%;
    top: 490px;
    text-align: center;
    font-size: 34px;
  }
  .back-web {
    position: absolute;
    left: 0;
    width: 100%;
    bottom: 26px;
    text-align: center;
    font-size: 23px;
    letter-spacing: 4px;
  }
</style>
</head>
<body>
  <section class="card card-front" aria-label="Business card front">
    <div class="brand-dot"></div>
    <div class="front-name">OBK</div>
    <div class="front-slogan">Bringing Trade Home</div>
    <div class="address">00, Complex Name, City, State, 00045</div>
    <div class="divider"></div>
    <div class="contact-band">
      <p class="person"><strong>Your Name,</strong> Position</p>
      <ul class="contact-list">
        <li>
          <svg viewBox="0 0 20 20" aria-hidden="true"><circle cx="10" cy="10" r="9" fill="none" stroke="#fff" stroke-width="2"/><path d="M6 5c1-1 2 0 2.5 1.5.3 1-.8 1.3-.4 2.2.6 1.3 1.6 2.3 2.9 2.9.9.4 1.2-.7 2.2-.4C14.7 11.7 15.5 13 14.5 14c-2.5 2-9-4.5-8.5-9z"/></svg>
          123-456-7890
        </li>
        <li>
          <svg viewBox="0 0 20 20" aria-hidden="true"><rect x="5" y="1" width="10" height="18" rx="2"/><rect x="7" y="4" width="6" height="7" fill="#1f7dbb"/></svg>
          123-456-7890
        </li>
        <li>
          <svg viewBox="0 0 20 20" aria-hidden="true"><rect x="1" y="5" width="18" height="12" rx="1"/><path d="M1 6l9 6 9-6" fill="none" stroke="#1f7dbb" stroke-width="1.6"/></svg>
          info@example-trade.com
        </li>
        <li>
          <svg viewBox="0 0 20 20" aria-hidden="true"><circle cx="10" cy="10" r="8.5" fill="none" stroke="#fff" stroke-width="1.8"/><ellipse cx="10" cy="10" rx="3.5" ry="8.5" fill="none" stroke="#fff" stroke-width="1.5"/><path d="M1.5 10h17M3 5.5h14M3 14.5h14" stroke="#fff" stroke-width="1.3"/></svg>
          www.example-trade.com
        </li>
      </ul>
    </div>
  </section>

  <section class="card card-back" aria-label="Business card back">
    <div class="back-dot"></div>
    <div class="back-name">OBK</div>
    <div class="back-slogan">Bringing Trade Home</div>
    <div class="back-web">www.example-trade.com</div>
  </section>
</body>
</html>
```